Broschüre
Zielgruppe
Die T.O.R.K. Lumen Holding GmbH ist ein inhabergeführtes Immobilienunternehmen mit Sitz in Moers. Wir sind spezialisiert auf den direkten Ankauf von Mehrfamilienhäusern, Wohnanlagen und größeren Wohnimmobilien in Nordrhein-Westfalen. Unser Schwerpunkt liegt auf einer schnellen, diskreten und unbürokratischen Abwicklung – vom ersten Kontakt bis zum notariellen Abschluss. Wir kaufen Objekte in jedem Zustand, ob vermietet, leerstehend oder sanierungsbedürftig.
Wer ist Deine Zielgruppe?
• Institutionelle Eigentümer z.b. Wohnungsunternehmen und Investoren, die Bestände veräußern wollen
Aufgabenstellung
• Corporate Identity: Seriös, modern, vertrauenswürdig. Die Broschüre soll unsere Professionalität und Diskretion betonen.
• Farben: Anlehnung an die Unternehmensfarben der T.O.R.K. Lumen Holding GmbH (dezent, elegant, z. B. dunkles Blau, Grau, Weiß; ggf. Akzentfarbe Gold oder ein warmes Gelb).
• Schriftarten: Gut lesbar, modern, ohne verschnörkelte Fonts.
• Format: Hochformat DIN A4, 4–8 Seiten, übersichtlich und klar strukturiert.
• Bildsprache: Hochwertige Immobilienbilder, urbane Aufnahmen aus NRW, Detailfotos (z. B. Architektur, Gebäudeansichten) sowie emotionale Motive, die Vertrauen und Sicherheit vermitteln.
• Ton & Stil: Seriös, diskret, aber sympathisch – nicht zu werblich, sondern lösungsorientiert.
• Logo: Unser Firmenlogo muss auf dem Titel und der Rückseite gut sichtbar platziert sein.

```html
<!DOCTYPE html>
<html lang="de">
<head>
<meta charset="utf-8">
<title>T.O.R.K. Lumen Holding – Broschüre</title>
<link href="https://fonts.googleapis.com/css2?family=Barlow:wght@300;400;500;600;700;800&display=swap" rel="stylesheet">
<style>
:root{
  --navy:#1b2545;
  --navy-card:#26315a;
  --gold:#c9a23a;
  --paper:#ffffff;
  --ink:#2b2f3a;
  --muted:#6b7080;
  --stage:#8c8c8c;
}
*{box-sizing:border-box;margin:0;padding:0}
html,body{width:1200px;height:4958px;overflow:hidden;background:var(--stage);font-family:'Barlow',sans-serif;color:var(--ink)}
.sheet{position:absolute;left:180px;width:840px;height:1188px;background:var(--paper);overflow:hidden;box-shadow:0 6px 24px rgba(0,0,0,.25)}
.sheet--cover{top:43px}
.sheet--back{top:1271px}
.sheet--inside-left{top:2499px}
.sheet--inside-right{top:3727px}
.band{position:absolute;left:0;right:0;bottom:0;background:var(--navy);border-top:4px solid var(--gold)}
.photo{position:absolute}
.brand{display:flex;align-items:center;gap:10px;color:var(--navy);font-weight:600}
.brand-mark{width:14px;height:14px;background:var(--gold)}
/* cover */
.cover-photo{left:0;top:0;width:840px;height:880px;background:linear-gradient(180deg,#7fb0e4 0%,#b9d4ef 30%,#9a6b45 52%,#7d5a3c 70%,#6f8f3e 88%,#5f7f35 100%)}
.cover-brand{position:absolute;top:60px;right:56px;font-size:22px;text-align:right}
.sheet--cover .band{top:880px}
.cover-kicker{position:absolute;left:56px;top:52px;font-size:54px;font-weight:300;color:var(--gold);letter-spacing:1px}
.cover-title{position:absolute;left:56px;top:112px;font-size:60px;font-weight:800;color:#fff;letter-spacing:.5px}
.cover-title em{font-style:normal;color:var(--gold)}
.cover-sub{position:absolute;left:56px;top:196px;font-size:16px;color:#fff}
/* back */
.back-brand{position:absolute;top:230px;left:0;right:0;justify-content:center;font-size:40px}
.back-brand .brand-mark{width:22px;height:22px}
.back-claim{position:absolute;top:560px;left:0;right:0;text-align:center;font-size:28px;font-weight:500;line-height:1.35;color:var(--ink)}
.back-note{position:absolute;top:660px;left:0;right:0;text-align:center;font-size:18px;color:var(--muted)}
.sheet--back .band{top:880px}
.contact-title{position:absolute;left:110px;top:120px;font-size:44px;font-weight:700;color:var(--gold)}
.contact-rule{position:absolute;left:330px;top:108px;width:3px;height:90px;background:var(--gold)}
.contact-list{position:absolute;left:360px;top:114px;list-style:none;color:#d8dbe6;font-size:16px}
.contact-list li{display:flex;align-items:center;gap:12px;margin-bottom:22px}
.contact-list svg{width:20px;height:20px;flex:none}
/* shared heading */
.h-section{font-size:34px;font-weight:500;color:var(--navy);line-height:1.15;letter-spacing:.5px}
.h-section span{display:block;color:var(--gold)}
.copy{font-size:13.5px;line-height:1.55;color:var(--muted)}
.copy p{margin-bottom:12px}
.band-title{font-size:28px;font-weight:500;color:#fff;line-height:1.25;letter-spacing:.5px}
.band-title span{display:block;color:var(--gold)}
/* inside left */
.portrait{left:40px;top:50px;width:300px;height:560px;background:linear-gradient(160deg,#dfe6ee 0%,#b8c6d6 45%,#3c4a6a 100%);clip-path:polygon(0 0,100% 0,100% 82%,55% 100%,0 82%)}
.intro{position:absolute;left:380px;top:70px;width:410px}
.intro .copy{margin-top:28px}
.sheet--inside-left .band{top:660px;border-top:none}
.steps-head{position:absolute;left:40px;top:40px}
.steps-lead{position:absolute;left:40px;top:130px;font-size:13px;color:#b7bccb}
.steps{position:absolute;left:40px;top:180px;width:760px;display:grid;grid-template-columns:1fr 1fr;gap:22px 30px}
.step-head{display:flex;align-items:center;gap:14px;font-size:15px;font-weight:600;color:#fff}
.step-icon{width:40px;height:40px;border-radius:50%;background:var(--gold);display:flex;align-items:center;justify-content:center;flex:none}
.step-icon svg{width:20px;height:20px}
.step p{margin-top:10px;font-size:13px;line-height:1.5;color:#b7bccb}
/* inside right */
.profile{position:absolute;left:40px;top:70px;width:380px}
.profile .copy{margin-top:30px}
.checklist{list-style:none;margin:16px 0}
.checklist li{position:relative;padding-left:24px;margin-bottom:14px}
.checklist li::before{content:"";position:absolute;left:0;top:5px;width:10px;height:10px;border-radius:50%;background:var(--gold)}
.copy strong{color:var(--ink);font-weight:600}
.building{left:450px;top:60px;width:350px;height:560px;background:linear-gradient(180deg,#8fbbe6 0%,#c6dcf2 32%,#9c5f3c 52%,#8a5434 75%,#6b9a45 100%)}
.sheet--inside-right .band{top:660px;border-top:none}
.notch{position:absolute;left:0;top:-1px;width:0;height:0;border-left:38px solid var(--gold);border-bottom:38px solid transparent}
.reviews-head{position:absolute;left:40px;top:40px}
.quote-mark{position:absolute;right:50px;top:10px;font-size:140px;font-weight:800;color:var(--gold);line-height:1}
.reviews{position:absolute;left:40px;top:180px;width:760px;display:grid;grid-template-columns:repeat(3,1fr);gap:18px}
.review{background:var(--navy-card);padding:20px 18px;height:300px}
.review-head{display:flex;align-items:center;gap:12px}
.avatar{width:38px;height:38px;border-radius:50%;background:var(--gold);color:var(--navy);font-weight:700;font-size:18px;display:flex;align-items:center;justify-content:center}
.review-name{font-size:15px;font-weight:600;color:#fff}
.review-role{font-size:11px;color:#9ea4b8}
.review p{margin-top:18px;font-size:13px;line-height:1.55;color:#c3c7d4}
</style>
</head>
<body>

<section class="sheet sheet--cover">
  <div class="photo cover-photo" role="img" aria-label="Foto: Mehrfamilienhaus aus Klinker mit Balkonen, Grünfläche und blauem Himmel"></div>
  <div class="brand cover-brand"><span class="brand-mark"></span>T.O.R.K. Lumen Holding</div>
  <div class="band">
    <div class="cover-kicker">WIR KAUFEN</div>
    <div class="cover-title">IMMOBILIEN IN <em>NRW</em></div>
    <div class="cover-sub">Wohnungsunternehmen | Privatverkäufer &amp; Erbengemeinschaften | Tippgeber werden</div>
  </div>
</section>

<section class="sheet sheet--back">
  <div class="brand back-brand"><span class="brand-mark"></span>T.O.R.K. Lumen Holding</div>
  <div class="back-claim">Verkaufen Sie Ihr Mehrfamilienhaus<br>an einen verlässlichen Partner</div>
  <div class="back-note">Unsere Erfahrung, unsere Zuverlässigkeit, Ihr Vorteil.</div>
  <div class="band">
    <div class="contact-title">Kontakt</div>
    <div class="contact-rule"></div>
    <ul class="contact-list">
      <li><svg viewBox="0 0 20 20"><rect width="20" height="20" fill="#c9a23a"/><path d="M10 4a4 4 0 0 0-4 4c0 3 4 8 4 8s4-5 4-8a4 4 0 0 0-4-4zm0 5.5A1.5 1.5 0 1 1 10 6.5a1.5 1.5 0 0 1 0 3z" fill="#1b2545"/></svg>Lindenallee 24 · 47441 Moers</li>
      <li><svg viewBox="0 0 20 20"><rect width="20" height="20" fill="#c9a23a"/><path d="M4 6h12v8H4z" fill="none" stroke="#1b2545" stroke-width="1.5"/><path d="M4 6l6 5 6-5" fill="none" stroke="#1b2545" stroke-width="1.5"/></svg>kontakt@tork-lumen.de</li>
    </ul>
  </div>
</section>

<section class="sheet sheet--inside-left">
  <div class="photo portrait" role="img" aria-label="Foto: Ansprechpartnerin im Büro vor Glasfassade"></div>
  <div class="intro">
    <h2 class="h-section">WIR INVESTIEREN<span>IN WERTE, DIE BLEIBEN.</span></h2>
    <div class="copy">
      <p>Als inhabergeführtes Unternehmen mit Sitz in Moers stehen wir für Verlässlichkeit, Diskretion und Handschlagqualität. Wir kaufen Wohnimmobilien direkt – von Wohnungsunternehmen, privaten Eigentümern, Erbengemeinschaften und institutionellen Verkäufern. Dabei zählen keine Versprechungen, sondern klare Entscheidungen.</p>
      <p>Wir wissen, dass jedes Objekt einzigartig ist. Deshalb setzen wir auf individuelle Lösungen, die genau zu Ihrer Situation passen. Ob vermietet, leerstehend oder sanierungsbedürftig – wir prüfen schnell und fair.</p>
      <p>Unser Hauptaugenmerk liegt auf Mehrfamilienhäusern sowie Wohnanlagen in den Städten Moers, Neukirchen-Vluyn, Kamp-Lintfort und Duisburg.</p>
    </div>
  </div>
  <div class="band">
    <h2 class="band-title steps-head">IMMOBILIE VERKAUFEN – EINFACH,<span>SCHNELL, SICHER</span></h2>
    <div class="steps-lead">Mit T.O.R.K. Lumen Holding ist der Immobilienverkauf unkompliziert und transparent.</div>
    <div class="steps">
      <div class="step">
        <div class="step-head"><span class="step-icon"><svg viewBox="0 0 20 20"><path d="M3 10l14-6-5 14-2-6z" fill="#1b2545"/></svg></span>Anfrage senden</div>
        <p>Sie senden uns die Eckdaten Ihrer Immobilie – online oder telefonisch.</p>
      </div>
      <div class="step">
        <div class="step-head"><span class="step-icon"><svg viewBox="0 0 20 20"><circle cx="10" cy="10" r="7" fill="none" stroke="#1b2545" stroke-width="2"/><path d="M10 6v4l3 2" fill="none" stroke="#1b2545" stroke-width="2"/></svg></span>Rückmeldung in 24h</div>
        <p>Wir melden uns schnellstmöglich bei Ihnen mit einer ersten Einschätzung.</p>
      </div>
      <div class="step">
        <div class="step-head"><span class="step-icon"><svg viewBox="0 0 20 20"><path d="M3 10l7-6 7 6v7H3z" fill="#1b2545"/></svg></span>Besichtigung &amp; Angebot</div>
        <p>Nach der Vor-Ort-Besichtigung erhalten Sie ein verbindliches Kaufangebot.</p>
      </div>
      <div class="step">
        <div class="step-head"><span class="step-icon"><svg viewBox="0 0 20 20"><path d="M4 10l4 4 8-8" fill="none" stroke="#1b2545" stroke-width="2.5"/></svg></span>Notartermin &amp; Verkauf</div>
        <p>Wir übernehmen alle Formalitäten – schnell, rechtssicher und ohne Provision.</p>
      </div>
    </div>
  </div>
</section>

<section class="sheet sheet--inside-right">
  <div class="profile">
    <h2 class="h-section">UNSER<span>ANKAUFSPROFIL</span></h2>
    <div class="copy">
      <p>Wir suchen gezielt Wohnimmobilien in NRW mit Fokus auf:</p>
      <ul class="checklist">
        <li>Mehrfamilienhäuser</li>
        <li>Lage: Moers, Duisburg, Kamp-Lintfort, Neukirchen-Vluyn und Umgebung</li>
        <li>Auch sanierungsbedürftige Objekte</li>
        <li>Wir kaufen direkt – vom kleineren Mehrfamilienhaus bis hin zu Wohnportfolios mit einem Volumen bis 10 Mio. €</li>
      </ul>
      <p>Ob kleinere Immobilie oder umfangreiches Wohnportfolio – wir prüfen jede Immobilie schnell, diskret und fair.<br><strong><em>Egal ob vermietet, leerstehend oder sanierungsbedürftig.</em></strong></p>
    </div>
  </div>
  <div class="photo building" role="img" aria-label="Foto: Klinker-Mehrfamilienhaus mit jungem Baum und Rasen"></div>
  <div class="band">
    <div class="notch"></div>
    <h2 class="band-title reviews-head">WAS SIE<span>ÜBER UNS SAGEN</span></h2>
    <div class="quote-mark">“</div>
    <div class="reviews">
      <article class="review">
        <div class="review-head"><span class="avatar">M</span><div><div class="review-name">M. Hartung</div><div class="review-role">Privatverkäufer</div></div></div>
        <p>„Innerhalb von zwei Wochen war der Kaufvertrag unterschrieben – das hätte ich nie für möglich gehalten. Der gesamte Prozess war professionell, schnell und vor allem unkompliziert.“</p>
      </article>
      <article class="review">
        <div class="review-head"><span class="avatar">J</span><div><div class="review-name">J. Roloff</div><div class="review-role">Erbengemeinschaft</div></div></div>
        <p>„Ich hatte zuerst Bedenken, meine Immobilie zu verkaufen, aber das Team hat sich viel Zeit genommen. Die Abwicklung war ehrlich und transparent.“</p>
      </article>
      <article class="review">
        <div class="review-head"><span class="avatar">T</span><div><div class="review-name">T. Brenner</div><div class="review-role">Wohnungsunternehmen</div></div></div>
        <p>„Ich hatte keine Erfahrung mit Immobilienverkäufen, aber das Team hat mich Schritt für Schritt begleitet. Alle Fragen wurden ausführlich beantwortet.“</p>
      </article>
    </div>
  </div>
</section>

</body>
</html>
```